New Business Card Design Project

We just had our logo designed and now are in need of business cards. The new logo is attached, we would like it to be double sided, and are open to design and layouts. (Standard business card size please) Our website is currently being worked on so if you need ideas as to what we do please look at www.lumatekcrew.com as its the same type of business

Industry/Entity Type

Remediation

Contact Information for Business Card

read above and below for details

Font styles to use
Other font styles liked:
• My Logo fonts are: font name "Airstrike Regular" 2nd line font name "Nexa Bold"

Colors

Designer to choose colors to be used in the design.

Requirements
Must have
• Name: Derek Hollowmere
• Title: Owner
• Address: 412 S. Birchfield Commerce Way #23 Ashcombe, RI 06817
• Phone: 203-617-2938
• Email: derek@tavrobuild.com
• website: www.tavrobuild.com
Nice to have
• Something that explains what we do so when you look at the card you'll know. We do the following:
• - Indoor Air Quality Testing
• - Fire & Smoke Damage
• - Water Damage & Sewer Backup
• - Storm Damage
• - Mold Remediation
• - General Contracting & Remodeling

```html
<!DOCTYPE html>
<html lang="en">
<head>
<meta charset="utf-8">
<title>Tavrobuild Business Cards</title>
<link href="https://fonts.googleapis.com/css2?family=Montserrat:wght@400;500;700;800&display=swap" rel="stylesheet">
<style>
  :root {
    --navy: #1f466b;
    --orange: #e8431f;
    --white: #ffffff;
    --ink: #3a3f47;
    --backdrop: #b9babd;
  }
  * { margin: 0; padding: 0; box-sizing: border-box; }
  html, body {
    width: 1200px; height: 852px; overflow: hidden;
    background: var(--backdrop);
    font-family: "Montserrat", Arial, sans-serif;
  }
  .sheet {
    width: 1200px; height: 852px;
    display: flex; align-items: center; justify-content: center; gap: 40px;
  }
  .card {
    width: 540px; height: 309px; position: relative; overflow: hidden;
    box-shadow: 0 6px 18px rgba(0,0,0,0.18);
  }
  /* Front */
  .card--front { background: var(--navy); color: var(--white); }
  .brand {
    position: absolute; left: 0; right: 0; top: 78px;
    display: flex; align-items: center; justify-content: center; gap: 12px;
  }
  .brand__square { width: 22px; height: 22px; background: var(--white); }
  .brand__name {
    font-weight: 800; font-size: 42px; letter-spacing: 1px;
    text-transform: uppercase; color: var(--orange);
  }
  .services {
    position: absolute; left: 0; right: 0; top: 200px;
    list-style: none; text-align: center; font-size: 13.5px; line-height: 1.75;
  }
  .services__row span { white-space: nowrap; }
  .services__row span + span { margin-left: 14px; }
  .services__row span::before {
    content: ""; display: inline-block; width: 6px; height: 6px; border-radius: 50%;
    background: var(--orange); margin-right: 5px; vertical-align: middle;
  }
  /* Back */
  .card--back { background: var(--white); }
  .card--back .brand {
    left: 300px; right: 20px; top: 0; bottom: 0; gap: 10px;
  }
  .card--back .brand__name { font-size: 30px; }
  .card--back .brand__square { width: 16px; height: 16px; background: var(--navy); }
  .marker {
    position: absolute; left: 0; top: 52px; width: 26px; height: 44px; background: var(--navy);
  }
  .person { position: absolute; left: 42px; top: 50px; width: 250px; }
  .person__name {
    color: var(--navy); font-weight: 700; font-size: 22px; line-height: 1.15;
    text-transform: uppercase; letter-spacing: 0.3px;
  }
  .person__title { color: var(--orange); font-size: 17px; font-weight: 400; margin-top: 2px; }
  .contact {
    position: absolute; left: 42px; top: 158px; width: 255px;
    color: var(--ink); font-size: 12.5px; line-height: 1.5;
  }
  .contact__address { margin-bottom: 10px; }
  .contact__list { list-style: none; }
  .contact__list li { display: flex; align-items: center; gap: 7px; }
  .contact__list svg { width: 12px; height: 12px; fill: none; stroke: var(--orange); stroke-width: 2; }
</style>
</head>
<body>
<main class="sheet">
  <section class="card card--front" aria-label="Card front">
    <div class="brand">
      <span class="brand__square"></span>
      <span class="brand__name">Tavrobuild</span>
    </div>
    <ul class="services">
      <li class="services__row"><span>Indoor Air Quality Testing</span><span>Fire, Water, Storm Damage Cleanup</span></li>
      <li class="services__row"><span>Mold Remediation</span><span>Restoration and Renovations</span></li>
    </ul>
  </section>

  <section class="card card--back" aria-label="Card back">
    <div class="marker"></div>
    <div class="person">
      <h1 class="person__name">Derek Hollowmere</h1>
      <p class="person__title">Owner</p>
    </div>
    <div class="contact">
      <p class="contact__address">412 S. Birchfield Commerce Way #23<br>Ashcombe, RI 06817</p>
      <ul class="contact__list">
        <li><svg viewBox="0 0 24 24"><path d="M5 3h4l2 5-3 2a12 12 0 0 0 6 6l2-3 5 2v4a2 2 0 0 1-2 2A17 17 0 0 1 3 5a2 2 0 0 1 2-2z"/></svg>203-617-2938</li>
        <li><svg viewBox="0 0 24 24"><rect x="3" y="5" width="18" height="14" rx="1"/><path d="M3 6l9 7 9-7"/></svg>derek@tavrobuild.com</li>
        <li><svg viewBox="0 0 24 24"><circle cx="12" cy="12" r="9"/><path d="M3 12h18M12 3c3 3 3 15 0 18M12 3c-3 3-3 15 0 18"/></svg>www.tavrobuild.com</li>
      </ul>
    </div>
    <div class="brand">
      <span class="brand__square"></span>
      <span class="brand__name">Tavrobuild</span>
    </div>
  </section>
</main>
</body>
</html>
```